High Tech Real Estate Startup needs a business card

We are developing an innovative real estate marketing product based around advanced search and virtual reality.

We talk to people, we need business cards.

Target Market(s)

The target market is technology professionals and realtors.

Contact Information for Business Card

The information to be included will include

Name
Title
Phone Number
E-mail Address
www.zelquin.com

It should use simple iconography for each one of those fields.

Font styles to use
Other font styles liked:
• Co, Jubilat, Avenir

Colors

Designer to choose colors to be used in the design.

Requirements
Must have
• Clean aesthetic,
• Good use of negative space.
• It should use our company logo, shown in the attached file. It is able to use the negative of that logo (coloured font and white background) and I have attached other acceptable accent colours in a swatch file.
Should not have
• Should not be too busy
• No extraneous text (slogans, tag lines etc)

```html
<!DOCTYPE html>
<html lang="en">
<head>
<meta charset="utf-8">
<title>Zelquin Business Card</title>
<link rel="stylesheet" href="https://fonts.googleapis.com/css2?family=Roboto:wght@400;500&family=Roboto+Condensed:wght@500&display=swap">
<style>
  :root {
    --teal: #03b9bd;
    --white: #ffffff;
    --paper: #f2f2f2;
    --ink: #444444;
    --rule: #6a6a6a;
    --band-grey: #6f6f6f;
    --backdrop: #252525;
    --url-light: #d9f4f5;
  }
  * { margin: 0; padding: 0; box-sizing: border-box; }
  html, body { width: 1200px; height: 960px; overflow: hidden; }
  body {
    background: var(--backdrop);
    font-family: "Roboto", Arial, sans-serif;
    position: relative;
  }
  .card {
    position: absolute;
    width: 600px;
    height: 342px;
    overflow: hidden;
  }
  /* Front */
  .card-front {
    left: 322px; top: 108px;
    background: var(--teal);
  }
  .card-front .wordmark {
    position: absolute;
    left: 0; right: 0; top: 128px;
    text-align: center;
    color: var(--white);
    font-weight: 500;
    font-size: 78px;
    line-height: 1;
    letter-spacing: 2px;
  }
  .card-front .website {
    position: absolute;
    left: 0; right: 0; top: 259px;
    text-align: center;
    color: var(--url-light);
    font-size: 14px;
    letter-spacing: 4.2px;
  }
  /* Back */
  .card-back {
    left: 320px; top: 493px;
    background: var(--paper);
  }
  .card-back .wordmark {
    position: absolute;
    right: 33px; top: 40px;
    color: var(--teal);
    font-weight: 500;
    font-size: 52px;
    line-height: 1;
    letter-spacing: 1px;
  }
  .person { position: absolute; left: 32px; top: 202px; }
  .person .name {
    font-family: "Roboto Condensed", "Arial Narrow", sans-serif;
    font-weight: 500;
    font-size: 24px;
    line-height: 1;
    color: var(--teal);
  }
  .person .role {
    margin-top: 6px;
    font-size: 15px;
    font-weight: 500;
    color: var(--ink);
  }
  .divider {
    position: absolute;
    left: 32px; top: 258px;
    width: 535px; height: 1px;
    background: var(--rule);
  }
  .contacts {
    position: absolute;
    left: 33px; top: 273px;
    list-style: none;
    font-size: 14px;
    color: var(--ink);
  }
  .contacts li {
    display: flex; align-items: center;
    height: 20px;
  }
  .contacts svg { width: 14px; height: 14px; margin-right: 8px; fill: var(--teal); }
  .card-back .website {
    position: absolute;
    right: 31px; top: 296px;
    font-size: 14px;
    letter-spacing: 1.2px;
    color: var(--ink);
  }
  .edge-band { position: absolute; left: 0; bottom: 0; width: 600px; height: 9px; }
</style>
</head>
<body>
  <section class="card card-front">
    <div class="wordmark">ZELQUIN</div>
    <div class="website">WWW.ZELQUIN.COM</div>
  </section>

  <section class="card card-back">
    <div class="wordmark">ZELQUIN</div>
    <div class="person">
      <div class="name">DANA ROWE</div>
      <div class="role">CEO/FOUNDER</div>
    </div>
    <div class="divider"></div>
    <ul class="contacts">
      <li>
        <svg viewBox="0 0 24 24" aria-hidden="true"><path d="M6.6 10.8a15.1 15.1 0 0 0 6.6 6.6l2.2-2.2c.3-.3.7-.4 1-.2 1.1.4 2.3.6 3.6.6.6 0 1 .4 1 1V20c0 .6-.4 1-1 1A17 17 0 0 1 3 4c0-.6.4-1 1-1h3.5c.6 0 1 .4 1 1 0 1.3.2 2.5.6 3.6.1.3 0 .7-.2 1z"/></svg>
        555 214 0187
      </li>
      <li>
        <svg viewBox="0 0 24 24" aria-hidden="true"><path d="M2 5h20v2l-10 6L2 7z"/><path d="M2 9l10 6 10-6v10H2z"/></svg>
        dana@zelquin.com
      </li>
    </ul>
    <div class="website">www.zelquin.com</div>
    <svg class="edge-band" viewBox="0 0 600 9" preserveAspectRatio="none" aria-hidden="true">
      <polygon points="0,0 392,0 389,9 0,9" fill="var(--teal)"/>
      <polygon points="396,0 600,0 600,9 393,9" fill="var(--band-grey)"/>
    </svg>
  </section>
</body>
</html>
```